BildeVOLD buisnesscard

Hey :) I need a modern buisnesscard for my company BildeVOLD
It most have:
Dagligleder og Fotograf: Henrik Audun Strandvik

Mob: +4791264085
Epost: post@bildevold.example
Adresse: Kvernbakken9, 6040 Langevåg

Facbook and instagram logo with text BildeVOLD

BildeVOLD logo

It Company

```html
<!DOCTYPE html>
<html lang="nb">
<head>
<meta charset="utf-8">
<title>BildeVOLD – visittkort</title>
<link rel="stylesheet" href="https://fonts.googleapis.com/css2?family=Montserrat:wght@400;500;600&display=swap">
<style>
  :root {
    --backdrop: #e6e7e8;
    --paper: #ffffff;
    --ink: #111111;
    --brand-grey: #a9abad;
    --band-grey: #b5b6b6;
    --back-black: #000000;
  }
  * { box-sizing: border-box; margin: 0; padding: 0; }
  html, body {
    width: 1200px; height: 927px; overflow: hidden;
    background: var(--backdrop);
    font-family: "Montserrat", sans-serif;
    color: var(--ink);
  }
  .sheet { position: relative; width: 1200px; height: 927px; }
  .card {
    position: absolute; top: 68px; width: 451px; height: 790px;
    box-shadow: 6px 6px 8px rgba(0,0,0,0.35);
  }
  .card--front { left: 126px; background: var(--paper); }
  .card--back { left: 623px; background: var(--back-black); }

  .brand {
    position: absolute; left: 0; right: 0; top: 160px;
    display: flex; justify-content: center; align-items: center; gap: 12px;
    font-weight: 600; font-size: 50px; color: var(--brand-grey); letter-spacing: 0.5px;
  }
  .brand__square { width: 34px; height: 34px; background: var(--brand-grey); }

  .identity {
    position: absolute; left: 59px; top: 410px; width: 333px; height: 49px;
    border: 1px solid var(--ink); text-align: center;
  }
  .identity__name {
    font-weight: 500; font-size: 25px; line-height: 1; margin-top: 7px; white-space: nowrap;
  }
  .identity__role {
    position: absolute; left: 50%; bottom: -10px; transform: translateX(-50%);
    background: var(--paper); padding: 0 4px; font-size: 16px; line-height: 18px; white-space: nowrap;
  }
  .contact-icons {
    position: absolute; left: 0; right: 0; top: 483px;
    display: flex; justify-content: center; gap: 6px;
  }
  .contact {
    position: absolute; left: 0; right: 0; top: 508px;
    text-align: center; font-size: 19px; line-height: 24.5px; list-style: none;
  }
  .social {
    position: absolute; left: 0; right: 0; top: 706px;
    display: flex; justify-content: center; gap: 8px;
  }
  .social__mark { width: 16px; height: 16px; background: var(--brand-grey); }
  .social-handle {
    position: absolute; left: 0; right: 0; top: 733px;
    text-align: center; font-size: 19px;
  }
  .bands { position: absolute; left: 0; bottom: 0; width: 451px; height: 22px; }
  .band { position: absolute; top: 0; height: 22px; }
  .band--left { left: 0; width: 89px; background: var(--band-grey); }
  .band--mid { left: 98px; width: 255px; background: var(--ink); }
  .band--right { left: 362px; width: 89px; background: var(--band-grey); }

  .back-brand {
    position: absolute; left: 0; right: 0; top: 370px;
    text-align: center; font-weight: 600; font-size: 56px; color: var(--brand-grey);
  }
</style>
</head>
<body>
<main class="sheet">
  <section class="card card--front" aria-label="Forside">
    <div class="brand"><span class="brand__square"></span><span>BildeVOLD</span></div>

    <div class="identity">
      <p class="identity__name">Henrik Audun Strandvik</p>
      <p class="identity__role">Dagligleder og Fotograf</p>
    </div>

    <div class="contact-icons" aria-hidden="true">
      <svg width="12" height="14" viewBox="0 0 12 14"><path d="M3 1 L5 4 L3.6 5.4 C4.4 7.6 5.6 9 7.6 10.2 L9 8.8 L11.5 11 L10 13 C5 12 1.5 8 1 3 Z" fill="none" stroke="#111" stroke-width="1.4" stroke-linejoin="round"/></svg>
      <svg width="14" height="14" viewBox="0 0 14 14"><rect x="1" y="3" width="12" height="8" fill="none" stroke="#111" stroke-width="1.4"/><path d="M1 3 L7 8 L13 3" fill="none" stroke="#111" stroke-width="1.4"/></svg>
      <svg width="10" height="14" viewBox="0 0 10 14"><path d="M5 13 C2 9 1 7 1 5 A4 4 0 0 1 9 5 C9 7 8 9 5 13 Z" fill="#111"/><circle cx="5" cy="5" r="1.5" fill="#fff"/></svg>
    </div>

    <ul class="contact">
      <li>+4791264085</li>
      <li>post@bildevold.example</li>
      <li>Kvernbakken9, 6040 Langevåg</li>
    </ul>

    <div class="social" aria-hidden="true">
      <span class="social__mark"></span><span class="social__mark"></span>
    </div>
    <p class="social-handle">BildeVOLD</p>

    <div class="bands" aria-hidden="true">
      <span class="band band--left"></span>
      <span class="band band--mid"></span>
      <span class="band band--right"></span>
    </div>
  </section>

  <section class="card card--back" aria-label="Bakside">
    <p class="back-brand">BildeVOLD</p>
  </section>
</main>
</body>
</html>
```